Skin cancer clinic services trifold brochure

Need trifold brochure listing skin cancer services our clinic provides, staff information, location and brief about skin cancer with colours similar to our web site www.Tolvarin.clinic. I will provide more information regarding services and staff but want this colourful and standout as it will be given to other referring doctors or patients

Target Market(s)

Age 40 to 80 years

Industry/Entity Type

Medical

Font styles to use
Serif

Colors

Designer to choose colors to be used in the design.

Requirements
Must have
• Logo, services, contact info, beach or sun look and colours similar to web site or logo

```html
<!DOCTYPE html>
<html lang="en">
<head>
<meta charset="utf-8">
<title>Tolvarin Skin Cancer Clinic – Trifold Brochure</title>
<link href="https://fonts.googleapis.com/css2?family=Crimson+Text:ital,wght@0,400;0,600;0,700;1,400&family=Allura&display=swap" rel="stylesheet">
<style>
:root{
  --orange:#e8701a;
  --orange-deep:#d2521a;
  --orange-red:#c8401a;
  --amber:#f2a22a;
  --yellow:#f7b733;
  --ink:#3a3a3a;
  --paper:#ffffff;
  --bg:#e4e4e4;
  --sunset-top:#f7b89a;
  --sunset-mid:#e9a59a;
  --sunset-low:#8f97a8;
}
*{box-sizing:border-box;margin:0;padding:0}
html,body{width:1200px;height:1200px;overflow:hidden;background:var(--bg)}
body{position:relative;font-family:"Crimson Text",serif;color:var(--ink)}
.sheet{position:absolute;left:270px;width:660px;height:498px;background:var(--paper);overflow:hidden}
.sheet--outside{top:62px}
.sheet--inside{top:622px}
.panel{position:absolute;top:0;height:498px;width:220px}
.panel--a{left:0}.panel--b{left:220px;width:222px}.panel--c{left:442px;width:218px}
.abs{position:absolute}
/* outside: about */
.about__title{left:14px;top:14px;font-size:17px;font-weight:700;color:var(--orange)}
.about__bar{left:88px;top:24px;width:120px;height:5px;background:var(--orange)}
.about__rule{left:0;top:40px;width:220px;height:3px;background:var(--orange)}
.about__photo{left:0;top:48px;width:216px;height:116px;background:linear-gradient(135deg,#d9dde0,#f1f2f3 55%,#c8cdd2)}
.about__text{left:14px;top:188px;width:196px;font-size:8.2px;line-height:1.32}
.about__text p{margin-bottom:8px}
.about__rule2{left:0;top:401px;width:220px;height:6px;background:var(--orange)}
.about__map{left:0;top:410px;width:216px;height:88px;background:linear-gradient(120deg,#e9ecef,#f6f6f4 50%,#dfe6ec)}
/* outside: skin cancer */
.cancer{background:linear-gradient(180deg,var(--orange) 0%,#ec8020 55%,var(--yellow) 100%)}
.cancer__title{left:21px;top:12px;font-size:15px;color:#3a2414}
.cancer__lead{left:21px;top:40px;font-size:8.5px;color:#3a2414}
.cancer__text{left:21px;top:62px;width:185px;font-size:7.6px;line-height:1.38;color:#3a2414}
.cancer__dot{border-radius:50%;background:var(--orange-deep)}
.cancer__photo{left:47px;top:198px;width:150px;height:170px;background:linear-gradient(160deg,#d7b78a,#b08a68 50%,#6a5a58)}
.cancer__callout{left:16px;top:150px;width:94px;height:94px;border-radius:50%;background:var(--orange-deep);display:flex;align-items:center;justify-content:center;text-align:center;color:#fff;font-weight:700;font-size:12.5px;line-height:1.15;padding:6px}
.contact__title{left:38px;top:374px;font-size:12px;color:#3a2414}
.contact__list{left:27px;top:402px;list-style:none;font-size:8.6px;line-height:1.72;color:#3a2414}
.contact__list li{display:flex;align-items:flex-start;gap:4px}
.contact__list svg{flex:none;margin-top:3px}
.contact__fax{color:#f6d28a}
/* outside: cover */
.cover{background:linear-gradient(180deg,var(--sunset-top) 0%,#f3c4a8 25%,var(--sunset-mid) 50%,#9fa3b4 70%,var(--sunset-low) 100%)}
.cover__name{left:0;width:218px;top:128px;text-align:center;font-size:26px;font-weight:600;color:#fff}
.cover__tagline{left:0;width:218px;top:360px;text-align:center;font-family:"Allura",cursive;font-size:32px;line-height:.9;color:#fff}
/* inside */
.bands{left:0;top:0}
.badge{border-radius:50%;background:var(--orange-deep);border:4px solid #fff;box-shadow:0 0 0 3px var(--amber);display:flex;align-items:center;justify-content:center;text-align:center;color:#fff;font-weight:700;font-size:12.5px;line-height:1.2}
.list{list-style:none;font-size:5.8px;line-height:1.3;color:#555}
.list li{position:relative;padding-left:22px;margin-bottom:7px}
.list li svg{position:absolute;left:0;top:0}
.list b{color:var(--orange);font-weight:600}
.staff__intro{left:18px;top:122px;width:190px;font-size:6.4px;line-height:1.3;color:#444}
.staff__list{left:20px;top:168px;list-style:none;font-size:7.4px;line-height:1.28}
.staff__list li{position:relative;padding-left:12px;margin-bottom:8px;color:var(--orange)}
.staff__list i{color:#444;display:block}
.staff__list svg{position:absolute;left:0;top:2px}
.staff__note{left:18px;top:330px;width:74px;font-size:6px;line-height:1.32;color:var(--orange)}
.staff__illus{left:92px;top:350px;width:118px;height:96px;background:linear-gradient(160deg,#f1a98a,#e7846a 45%,#f3c261)}
</style>
</head>
<body>

<!-- OUTSIDE SHEET -->
<section class="sheet sheet--outside">
  <article class="panel panel--a about">
    <h2 class="abs about__title">About Us</h2>
    <div class="abs about__bar"></div>
    <div class="abs about__rule"></div>
    <div class="abs about__photo" role="img" aria-label="Photo of a clinician in mask and gloves inspecting a sample in a clinic"></div>
    <div class="abs about__text">
      <p>Tolvarin Skin Cancer Clinic is a purpose-built skin cancer clinic dedicated to providing the highest-level patient care to the Northern Bay community and surrounding regions.</p>
      <p>Our skilled doctors and nurses have extensive experience and advanced training in Skin Cancer Medicine in order to provide quality care to our patients. We specialise in a comprehensive approach to skin with preventive skin cancer care, expert diagnostic dermoscopy skills highlighting artificial intelligent analytics, and definitive surgical and medical treatments of skin cancers.</p>
      <p>Skin cancer medicine is all we do.</p>
      <p>We welcome you to “virtually” walk through our clinic at www.Tolvarin.clinic</p>
    </div>
    <div class="abs about__rule2"></div>
    <div class="abs about__map" role="img" aria-label="Street map showing the clinic location"></div>
  </article>

  <article class="panel panel--b cancer">
    <div class="abs cancer__dot" style="left:133px;top:3px;width:42px;height:42px"></div>
    <div class="abs cancer__dot" style="left:194px;top:22px;width:14px;height:14px"></div>
    <div class="abs cancer__dot" style="left:184px;top:51px;width:24px;height:24px"></div>
    <div class="abs cancer__dot" style="left:122px;top:158px;width:42px;height:42px"></div>
    <div class="abs cancer__dot" style="left:172px;top:176px;width:16px;height:16px"></div>
    <h2 class="abs cancer__title">Skin Cancer</h2>
    <p class="abs cancer__lead">Did you know?</p>
    <p class="abs cancer__text">Skin Cancers account for 80% of all newly diagnosed cancers with two in three Australians diagnosed with skin cancer by the time they are 70. Although over 90% of skin cancers are due to over exposure to UV light, some are caused by chemical exposure or are hereditary. Over 2000 Australians die from skin cancer each year.</p>
    <div class="abs cancer__photo" role="img" aria-label="Photo of a smiling older couple"></div>
    <div class="abs cancer__callout">Have you had your skin checked lately?</div>
    <h3 class="abs contact__title">Contact Us</h3>
    <ul class="abs contact__list">
      <li><svg width="7" height="9" viewBox="0 0 7 9"><path d="M3.5 0A3.5 3.5 0 0 0 0 3.5C0 6 3.5 9 3.5 9S7 6 7 3.5A3.5 3.5 0 0 0 3.5 0z" fill="var(--orange-deep)"/></svg><span>Suite 1 &amp; 2, 317 Harbour Road<br>Kinmore, NSW 2260</span></li>
      <li><svg width="7" height="7" viewBox="0 0 7 7"><path d="M1 0l1.6 1.8-.8 1a4 4 0 0 0 1.8 1.7l.9-.8L7 5.4 6 7C3 7 0 4 0 1z" fill="var(--orange-deep)"/></svg><span>1300 555 014</span></li>
      <li><svg width="7" height="7" viewBox="0 0 7 7"><path d="M1 0l1.6 1.8-.8 1a4 4 0 0 0 1.8 1.7l.9-.8L7 5.4 6 7C3 7 0 4 0 1z" fill="var(--orange-deep)"/></svg><span>4300 5562 <span class="contact__fax">FAX</span></span></li>
      <li><svg width="8" height="6" viewBox="0 0 8 6"><rect width="8" height="6" fill="var(--orange-deep)"/><path d="M0 0l4 3.4L8 0" stroke="#f6c46a" fill="none" stroke-width=".8"/></svg><span>admin@tolvarin.clinic</span></li>
      <li><svg width="8" height="8" viewBox="0 0 8 8"><circle cx="4" cy="4" r="3.5" fill="none" stroke="var(--orange-deep)"/><path d="M.5 4h7M4 .5c-2 2-2 5 0 7M4 .5c2 2 2 5 0 7" stroke="var(--orange-deep)" fill="none" stroke-width=".7"/></svg><span>www.Tolvarin.clinic</span></li>
    </ul>
  </article>

  <article class="panel panel--c cover" role="img" aria-label="Sunset over a calm beach with wet sand and rocks">
    <p class="abs cover__name">Tolvarin</p>
    <p class="abs cover__tagline">Comfort<br>In Your Skin</p>
  </article>
</section>

<!-- INSIDE SHEET -->
<section class="sheet sheet--inside">
  <svg class="abs bands" width="660" height="498" viewBox="0 0 660 498" aria-hidden="true">
    <rect width="660" height="498" fill="#fff"/>
    <path d="M442 0H660V498H442Z" fill="#fff"/>
    <!-- top bands -->
    <path d="M0 0H220V38L0 88Z" fill="var(--orange)"/>
    <path d="M0 62L220 22V36L0 100Z" fill="var(--amber)"/>
    <path d="M220 0H442V78L330 35L220 50Z" fill="var(--orange)"/>
    <path d="M220 22L330 28L442 60V78L330 38L220 50Z" fill="var(--orange-red)"/>
    <path d="M442 0H660V58L442 88Z" fill="var(--orange)"/>
    <path d="M442 70L660 40V50L442 88Z" fill="var(--amber)"/>
    <!-- bottom bands -->
    <path d="M0 470L220 440V498H0Z" fill="var(--orange)"/>
    <path d="M0 458L220 426V440L0 470Z" fill="var(--amber)"/>
    <path d="M220 420L442 468V498H220Z" fill="var(--orange)"/>
    <path d="M220 410L442 455V468L220 420Z" fill="var(--orange-red)"/>
    <path d="M442 478L660 438V498H442Z" fill="var(--orange)"/>
    <path d="M442 468L660 424V438L442 478Z" fill="var(--amber)"/>
    <!-- fold shading -->
    <rect x="216" y="0" width="6" height="498" fill="#000" opacity=".05"/>
    <rect x="440" y="0" width="6" height="498" fill="#000" opacity=".07"/>
  </svg>

  <div class="abs badge" style="left:52px;top:12px;width:92px;height:92px">Professional<br>Skin<br>Services</div>
  <div class="abs badge" style="left:288px;top:15px;width:88px;height:88px">Specialised<br>Treatments</div>
  <div class="abs badge" style="left:518px;top:24px;width:74px;height:74px">Our<br>Staff</div>

  <ul class="abs list" style="left:8px;top:120px;width:204px">
    <li><svg width="14" height="14" viewBox="0 0 14 14"><circle cx="7" cy="7" r="3" fill="none" stroke="var(--orange)"/><path d="M7 0v2.5M7 11.5V14M0 7h2.5M11.5 7H14M2 2l1.8 1.8M10.2 10.2L12 12M2 12l1.8-1.8M10.2 3.8L12 2" stroke="var(--orange)" stroke-width=".7"/></svg><b>Advanced Skin Cancer Detection</b> with detailed Full Body skin checks using dermoscopy and technology to minimise unnecessary excisions.</li>
    <li><svg width="14" height="14" viewBox="0 0 14 14"><circle cx="7" cy="7" r="3" fill="none" stroke="var(--orange)"/><path d="M7 0v2.5M7 11.5V14M0 7h2.5M11.5 7H14M2 2l1.8 1.8M10.2 10.2L12 12M2 12l1.8-1.8M10.2 3.8L12 2" stroke="var(--orange)" stroke-width=".7"/></svg><b>Individual Mole mapping and full body photography</b> utilising intelligent skin analytics with DermaTrace – an artificial intelligence-powered platform which provides tools for documenting and diagnosing skin cancers and evidence-based care. Powered by AI algorithms, it will identify changes to the skin over time and support early clinical decisions and diagnosis.</li>
    <li><svg width="14" height="14" viewBox="0 0 14 14"><circle cx="7" cy="7" r="3" fill="none" stroke="var(--orange)"/><path d="M7 0v2.5M7 11.5V14M0 7h2.5M11.5 7H14M2 2l1.8 1.8M10.2 10.2L12 12M2 12l1.8-1.8M10.2 3.8L12 2" stroke="var(--orange)" stroke-width=".7"/></svg><b>NaevaScan Skin Imaging System</b> which captures high-quality images using SpectraView – clinically proven technology which provides a unique level of detail and information from up to 2mm beneath the skin's surface allowing deeper assessment and risk of melanoma.</li>
    <li><svg width="14" height="14" viewBox="0 0 14 14"><circle cx="7" cy="7" r="3" fill="none" stroke="var(--orange)"/><path d="M7 0v2.5M7 11.5V14M0 7h2.5M11.5 7H14M2 2l1.8 1.8M10.2 10.2L12 12M2 12l1.8-1.8M10.2 3.8L12 2" stroke="var(--orange)" stroke-width=".7"/></svg><b>Purpose Built Skin Cancer Facility</b> providing Surgical treatments in 2 dedicated fully equipped theatres and Treatment room staffed by skilled skin cancer medicine nurses</li>
    <li><svg width="14" height="14" viewBox="0 0 14 14"><circle cx="7" cy="7" r="3" fill="none" stroke="var(--orange)"/><path d="M7 0v2.5M7 11.5V14M0 7h2.5M11.5 7H14M2 2l1.8 1.8M10.2 10.2L12 12M2 12l1.8-1.8M10.2 3.8L12 2" stroke="var(--orange)" stroke-width=".7"/></svg><b>Large referral basis</b> for our patients that may require extensive therapy for their skin cancers, including Radiotherapy for cosmetically sensitive areas that are not optimally treated with surgery, Advanced care under the Melanoma Unit and Mohs Surgery and more.</li>
    <li><svg width="14" height="14" viewBox="0 0 14 14"><circle cx="7" cy="7" r="3" fill="none" stroke="var(--orange)"/><path d="M7 0v2.5M7 11.5V14M0 7h2.5M11.5 7H14M2 2l1.8 1.8M10.2 10.2L12 12M2 12l1.8-1.8M10.2 3.8L12 2" stroke="var(--orange)" stroke-width=".7"/></svg><b>Priority Spot Checks</b> – appointments are set aside every day for urgent suspicious lesions allowing for quick evaluation, whether for an existing or new patient. Although we welcome GP referrals, it is not required.</li>
    <li><svg width="14" height="14" viewBox="0 0 14 14"><circle cx="7" cy="7" r="3" fill="none" stroke="var(--orange)"/><path d="M7 0v2.5M7 11.5V14M0 7h2.5M11.5 7H14M2 2l1.8 1.8M10.2 10.2L12 12M2 12l1.8-1.8M10.2 3.8L12 2" stroke="var(--orange)" stroke-width=".7"/></svg><b>GP Team Approach</b> – Tolvarin believes it is important that an integrated team approach to a patient's skin cancer care is important, and communication of histological results and findings are shared with their GP upon permission.</li>
    <li><svg width="14" height="14" viewBox="0 0 14 14"><circle cx="7" cy="7" r="3" fill="none" stroke="var(--orange)"/><path d="M7 0v2.5M7 11.5V14M0 7h2.5M11.5 7H14M2 2l1.8 1.8M10.2 10.2L12 12M2 12l1.8-1.8M10.2 3.8L12 2" stroke="var(--orange)" stroke-width=".7"/></svg><b>Pain minimisation Techniques</b> – Topical numbing creams and ChillPoint numbing agents are available to minimise tenderness that can come with local anaesthetics. Our theatres are equipped with overhead projectors playing calming nature scenes to ensure our patients are comfortable.</li>
  </ul>

  <ul class="abs list" style="left:228px;top:120px;width:206px">
    <li><svg width="14" height="14" viewBox="0 0 14 14"><circle cx="7" cy="7" r="3" fill="none" stroke="var(--orange)"/><path d="M7 0v2.5M7 11.5V14M0 7h2.5M11.5 7H14M2 2l1.8 1.8M10.2 10.2L12 12M2 12l1.8-1.8M10.2 3.8L12 2" stroke="var(--orange)" stroke-width=".7"/></svg><b>Surgical Procedures</b> – Our Doctors are proficient in surgical procedures from simple diagnostic biopsies or elliptical excisions to advanced procedures including skin grafts and surgical flap repair, all under a local anaesthetic.</li>
    <li style="margin-top:12px"><svg width="14" height="14" viewBox="0 0 14 14"><circle cx="7" cy="7" r="3" fill="none" stroke="var(--orange)"/><path d="M7 0v2.5M7 11.5V14M0 7h2.5M11.5 7H14M2 2l1.8 1.8M10.2 10.2L12 12M2 12l1.8-1.8M10.2 3.8L12 2" stroke="var(--orange)" stroke-width=".7"/></svg><b>RadiaCut Radiofrequency procedures</b> – Surgical options include a high frequency radiosurgical device for scalpel-less surgery. It allows our Doctors to use Radiowaves instead of scalpels to provide advanced skin cancer surgical procedures or cosmetic procedures; including removal of spider veins or vascular lesions and benign non-suspicious moles, skin tags, seborrheic keratoses, warts and other raised lesions. A RadiaCut procedure ensures minimal thermal tissue damage, bleeding, and recovery time, thus enhancing cosmetic outcome.</li>
    <li style="margin-top:12px"><svg width="14" height="14" viewBox="0 0 14 14"><circle cx="7" cy="7" r="3" fill="none" stroke="var(--orange)"/><path d="M7 0v2.5M7 11.5V14M0 7h2.5M11.5 7H14M2 2l1.8 1.8M10.2 10.2L12 12M2 12l1.8-1.8M10.2 3.8L12 2" stroke="var(--orange)" stroke-width=".7"/></svg><b>Margin Controlled Surgery</b><br>(also known as Slow Mohs or Delayed Closure) – a process where aggressive skin cancers are not closed after excision until the histological status and clearance is known. This can minimise the need for larger excisions and potentially benefit cosmetic outcome; especially in cosmetically sensitive regions such as the nose, ears and face.</li>
    <li style="margin-top:12px"><svg width="14" height="14" viewBox="0 0 14 14"><circle cx="7" cy="7" r="3" fill="none" stroke="var(--orange)"/><path d="M7 0v2.5M7 11.5V14M0 7h2.5M11.5 7H14M2 2l1.8 1.8M10.2 10.2L12 12M2 12l1.8-1.8M10.2 3.8L12 2" stroke="var(--orange)" stroke-width=".7"/></svg><b>Non-surgical treatments and preventative therapy options</b> – Our goal is to prevent and treat skin cancer in the least invasive way possible as appropriate. This includes preventative care including Vitamin B3 benefits and sun safe practices – to topical therapies, such as liquid nitrogen and prescriptive therapy for solar keratoses or superficial Non-Melanoma skin cancers.</li>
    <li style="margin-top:12px"><svg width="14" height="14" viewBox="0 0 14 14"><circle cx="7" cy="7" r="3" fill="none" stroke="var(--orange)"/><path d="M7 0v2.5M7 11.5V14M0 7h2.5M11.5 7H14M2 2l1.8 1.8M10.2 10.2L12 12M2 12l1.8-1.8M10.2 3.8L12 2" stroke="var(--orange)" stroke-width=".7"/></svg><b>Cosmetic Services</b> – Tolvarin approaches our skin cancer patient holistically and, by appointment, we can offer advice and treatment regarding skin pigmentation, troublesome bumps and lumps and more!</li>
    <li style="padding-left:0;margin-top:12px">Please see our web site at www.tolvarin.clinic for more information.</li>
  </ul>

  <p class="abs staff__intro" style="left:460px">At Tolvarin Skin Cancer Clinic, our highly qualified administrative staff, nurses and doctors are an integral part of the team ensuring excellent clinical care is provided to our patients. We currently have 5 experienced local doctors:</p>
  <ul class="abs staff__list" style="left:462px">
    <li><svg width="8" height="10" viewBox="0 0 8 10"><path d="M1 0v4a3 3 0 0 0 6 0V0M4 7v3" fill="none" stroke="#666" stroke-width=".9"/></svg>Dr. Maren Holt, BMed, FRACGP,<i>Diploma Skin Cancer Medicine/Surgery,<br>Diploma Aesthetic Medicine</i></li>
    <li><svg width="8" height="10" viewBox="0 0 8 10"><path d="M1 0v4a3 3 0 0 0 6 0V0M4 7v3" fill="none" stroke="#666" stroke-width=".9"/></svg>Dr. Priya Castell, BMed, FRACGP,<i>Diploma Skin Cancer Medicine/Surgery</i></li>
    <li><svg width="8" height="10" viewBox="0 0 8 10"><path d="M1 0v4a3 3 0 0 0 6 0V0M4 7v3" fill="none" stroke="#666" stroke-width=".9"/></svg>Dr. Helena Varga, MBBS, FRACGP</li>
    <li><svg width="8" height="10" viewBox="0 0 8 10"><path d="M1 0v4a3 3 0 0 0 6 0V0M4 7v3" fill="none" stroke="#666" stroke-width=".9"/></svg>Dr. Owen Telford, MBBS (Syd), Dip Law</li>
    <li><svg width="8" height="10" viewBox="0 0 8 10"><path d="M1 0v4a3 3 0 0 0 6 0V0M4 7v3" fill="none" stroke="#666" stroke-width=".9"/></svg>Dr. Ruth Ashdown, MBBS (Hons), FRACGP,<i>Cert. Skin Cancer Medicine</i></li>
  </ul>
  <p class="abs staff__note" style="left:458px">Early detection of skin cancers is vital for the best outcome. Tolvarin has invested in technology and research to provide the latest diagnostic services and treatments to meet the needs of our patients.</p>
  <div class="abs staff__illus" style="left:532px" role="img" aria-label="Cross-section illustration of skin layers with a lesion"></div>
</section>

</body>
</html>
```